SOLVE Study flyer

I need help designing a flyer for a research study that will include brain imaging in adolescents. The info is in the attached document. The study is called the Sequoia Outlook Lantern Valley Echo (SOLVE) study. Ideally this would be returned as a document that I can edit in the future as we will have several new recruitment phases (different age groups, etc. I also would love to have a logo designed as part of this project, but I recognize that might be a separate design request.

```html
<!DOCTYPE html>
<html lang="en">
<head>
<meta charset="utf-8">
<title>SOLVE Study – Recruitment Flyer</title>
<link href="https://fonts.googleapis.com/css2?family=Poppins:wght@400;500;600;700;800&family=Anton&family=Abril+Fatface&display=swap" rel="stylesheet">
<style>
  :root{
    --navy:#0b2a8f;
    --navy-deep:#0a1a4a;
    --ink:#111111;
    --text:#1b1b2a;
    --yellow:#fdb81e;
    --red:#c40d0d;
    --panel:#f1f1f2;
    --rule:#8a8a95;
    --white:#ffffff;
  }
  *{margin:0;padding:0;box-sizing:border-box}
  html,body{width:935px;height:1200px;overflow:hidden;background:var(--white)}
  body{font-family:"Poppins",sans-serif;color:var(--text)}
  .flyer{position:relative;width:935px;height:1200px;overflow:hidden;background:var(--white)}
  .abs{position:absolute}

  .hero-art{position:absolute;left:0;top:0}
  .title{left:57px;top:78px;font-size:48px;font-weight:700;color:var(--ink);letter-spacing:-0.5px}
  .ask-1{left:58px;top:146px;font-size:35px;font-weight:400;color:var(--ink);letter-spacing:0.5px}
  .ask-2{left:58px;top:188px;font-size:39px;font-weight:700;color:var(--ink);letter-spacing:-0.5px}
  .ask-rule{left:312px;top:232px;width:122px;height:1px;background:var(--rule)}
  .age{left:56px;top:222px;font-family:"Anton",sans-serif;font-size:90px;line-height:1.1;color:var(--yellow);letter-spacing:-1px}
  .worry{left:58px;top:333px;font-size:21px;font-weight:600;color:var(--ink)}
  .pill{left:57px;top:372px;width:318px;height:52px;border-radius:26px;background:var(--navy);color:var(--white);font-size:21px;font-weight:600;display:flex;align-items:center;justify-content:center}

  .badge{left:483px;top:259px;width:176px;height:176px;border-radius:50%;background:var(--red);border:3px solid var(--white);box-shadow:0 0 0 2px var(--red);display:flex;flex-direction:column;align-items:center;justify-content:center;color:var(--white);text-align:center}
  .badge-label{font-size:12.5px;font-weight:600;letter-spacing:0.2px}
  .badge-upto{font-family:"Abril Fatface",serif;font-size:25px;line-height:1;color:var(--yellow);margin-top:2px}
  .badge-amount{font-family:"Anton",sans-serif;font-size:44px;line-height:1.05;color:var(--yellow)}
  .badge-amount sup{font-size:22px;vertical-align:top;position:relative;top:4px}

  .info-panel{left:58px;top:463px;width:818px;height:274px;background:var(--panel);border-radius:10px}
  .lead{left:94px;top:501px;width:760px;font-size:17px;line-height:22px;color:var(--ink)}
  .section-head{left:94px;top:580px;font-size:24px;font-weight:700;color:var(--navy-deep)}
  .section-rule{left:515px;top:606px;width:320px;height:1px;background:var(--rule)}

  .step{top:638px;width:233px;height:238px;background:var(--white);border:2.5px solid var(--navy-deep);border-radius:6px;padding:5px}
  .step-inner{width:100%;height:100%;border:1px solid var(--navy-deep);border-radius:4px;display:flex;flex-direction:column;align-items:center;padding-top:20px}
  .step.highlight{border-color:var(--yellow)}
  .step.highlight .step-inner{border-color:var(--yellow)}
  .step-icon{width:64px;height:56px}
  .step-text{margin-top:20px;font-size:14px;line-height:16.5px;text-align:center;color:var(--ink);padding:0 8px}
  .step-1{left:98px}.step-2{left:348px}.step-3{left:598px}

  .kids-photo{left:20px;top:812px;width:330px;height:248px;border-radius:120px 140px 0 0;background:linear-gradient(90deg,#29a8d8 0%,#a7a9ad 30%,#f0c23a 58%,#1f2d5a 82%,#c8b38a 100%);opacity:0.9}

  .elig-head{left:364px;top:906px;font-size:26px;font-weight:700;color:var(--navy-deep);letter-spacing:-0.2px}
  .elig{top:969px;display:flex;flex-direction:column;align-items:center;text-align:center;font-size:13.5px;line-height:16px;color:var(--ink)}
  .elig svg{margin-bottom:8px}
  .elig-1{left:358px;width:100px}
  .elig-2{left:462px;width:196px}
  .elig-3{left:660px;width:230px;top:966px}
  .elig-divider{top:967px;width:1px;height:71px;background:var(--rule)}

  .contact-head{left:378px;top:1066px;font-size:29px;font-weight:700;color:var(--navy)}
  .phone{left:677px;top:1068px;display:flex;align-items:center;gap:4px;font-size:30px;font-weight:500;color:var(--ink);line-height:1}

  .band-yellow{left:0;top:1112px;width:935px;height:88px;background:var(--yellow)}
  .band-navy{left:0;top:0}
  .cta{left:50px;top:1111px;font-size:20px;font-weight:700;line-height:25px}
  .cta .accent{color:var(--yellow)}
  .cta .plain{color:var(--white)}
  .link{top:1134px;display:flex;align-items:center;gap:7px;font-size:14px;font-weight:500;color:var(--ink)}
  .link-email{left:408px}
  .link-web{left:650px}
</style>
</head>
<body>
<main class="flyer">

  <svg class="hero-art" width="935" height="480" viewBox="0 0 935 480" role="img" aria-label="Glowing blue brain visualised over a network of connected points">
    <defs>
      <radialGradient id="brainGlow" cx="0.5" cy="0.45" r="0.6">
        <stop offset="0" stop-color="#2fb6ff"/>
        <stop offset="0.45" stop-color="#1553c9"/>
        <stop offset="1" stop-color="#0a1a5e"/>
      </radialGradient>
    </defs>
    <circle cx="735" cy="190" r="258" fill="var(--navy)"/>
    <circle cx="735" cy="190" r="244" fill="var(--white)"/>
    <circle cx="738" cy="190" r="240" fill="url(#brainGlow)"/>
  </svg>

  <h1 class="abs title">SOLVE Study</h1>
  <p class="abs ask-1">ARE YOU THE PARENT</p>
  <p class="abs ask-2">of a CHILD</p>
  <span class="abs ask-rule"></span>
  <p class="abs age">AGE 10-17?</p>
  <p class="abs worry">DO THEY WORRY OR OVERTHINK</p>
  <p class="abs pill">NEGATIVE EMOTIONS?</p>

  <div class="abs badge">
    <span class="badge-label">COMPENSATION</span>
    <span class="badge-upto">UP TO</span>
    <span class="badge-amount"><sup>$</sup>140</span>
  </div>

  <div class="abs info-panel"></div>
  <p class="abs lead">Ridgefield University researchers are seeking girls age 10-17 for a study about brain activity in emotions and decision-making and how they relate to puberty, anxiety and depression.</p>
  <h2 class="abs section-head">Study participation involves</h2>
  <span class="abs section-rule"></span>

  <div class="abs step step-1"><div class="step-inner">
    <svg class="step-icon" viewBox="0 0 64 56" fill="var(--navy)">
      <rect x="4" y="20" width="44" height="30" rx="3" fill="none" stroke="var(--navy)" stroke-width="4"/>
      <rect x="0" y="48" width="52" height="5" rx="2"/>
      <circle cx="26" cy="32" r="5"/>
      <path d="M16 48c0-7 4-10 10-10s10 3 10 10z"/>
      <rect x="32" y="2" width="30" height="20" rx="4"/>
      <path d="M38 21l-3 8 9-8z"/>
      <circle cx="40" cy="12" r="2" fill="#fff"/><circle cx="47" cy="12" r="2" fill="#fff"/><circle cx="54" cy="12" r="2" fill="#fff"/>
    </svg>
    <p class="step-text">One one-hour interview (online or in-person) where your child will discuss their thoughts</p>
  </div></div>

  <div class="abs step step-2 highlight"><div class="step-inner">
    <svg class="step-icon" viewBox="0 0 64 56">
      <rect x="24" y="6" width="30" height="46" rx="2" fill="#f29a12"/>
      <rect x="16" y="0" width="30" height="46" rx="2" fill="var(--yellow)"/>
      <g stroke="#fff" stroke-width="2.5"><line x1="21" y1="10" x2="41" y2="10"/><line x1="21" y1="17" x2="41" y2="17"/><line x1="21" y1="24" x2="41" y2="24"/><line x1="21" y1="31" x2="41" y2="31"/><line x1="21" y1="38" x2="34" y2="38"/></g>
    </svg>
    <p class="step-text">Online questionnaires<br>(parent and child)</p>
  </div></div>

  <div class="abs step step-3"><div class="step-inner">
    <svg class="step-icon" viewBox="0 0 64 56" fill="var(--navy)">
      <circle cx="32" cy="24" r="24"/>
      <circle cx="32" cy="24" r="14" fill="#fff"/>
      <rect x="8" y="40" width="48" height="14" rx="2"/>
      <circle cx="32" cy="20" r="4"/>
      <path d="M27 44v-14h10v14z" fill="#fff"/>
      <path d="M29 42v-11h6v11z"/>
    </svg>
    <p class="step-text">One two-hour visit where your child will complete an MRI scan, answer questions about their puberty stage, and have a small hair sample taken to study puberty hormones</p>
  </div></div>

  <div class="abs kids-photo" role="img" aria-label="Photo of four smiling children standing together"></div>

  <h2 class="abs elig-head">Your child may be eligible if they</h2>
  <div class="abs elig elig-1">
    <svg width="16" height="16" viewBox="0 0 16 16"><circle cx="8" cy="8" r="8" fill="var(--yellow)"/><path d="M4.5 8.2l2.4 2.3 4.6-4.8" fill="none" stroke="#fff" stroke-width="1.8"/></svg>
    <span>Are age 10-17</span>
  </div>
  <span class="abs elig-divider" style="left:459px"></span>
  <div class="abs elig elig-2">
    <svg width="16" height="16" viewBox="0 0 16 16"><circle cx="8" cy="8" r="8" fill="var(--yellow)"/><path d="M4.5 8.2l2.4 2.3 4.6-4.8" fill="none" stroke="#fff" stroke-width="1.8"/></svg>
    <span>Tend to worry or over think negative thoughts</span>
  </div>
  <span class="abs elig-divider" style="left:658px"></span>
  <div class="abs elig elig-3">
    <svg width="16" height="16" viewBox="0 0 16 16"><circle cx="8" cy="8" r="8" fill="var(--yellow)"/><path d="M4.5 8.2l2.4 2.3 4.6-4.8" fill="none" stroke="#fff" stroke-width="1.8"/></svg>
    <span>have not been diagnosed with psychosis, learning problems, or autism</span>
  </div>

  <p class="abs contact-head">Please Contact Us</p>
  <p class="abs phone">
    <svg width="30" height="30" viewBox="0 0 30 30"><circle cx="15" cy="15" r="15" fill="var(--navy)"/><path d="M10 8c1-1 2-1 3 0l1.5 2.5c.5 1 0 1.8-.8 2.4 1 2 2.4 3.4 4.4 4.4.6-.8 1.4-1.3 2.4-.8L23 18c1 1 1 2 0 3-1.5 1.5-3.5 1.8-6 .5-3.5-2-6-4.5-8-8-1.3-2.5-1-4.5 1-5.5z" fill="#fff"/></svg>
    1555012840
  </p>

  <div class="abs band-yellow"></div>
  <svg class="abs band-navy" width="935" height="1200" viewBox="0 0 935 1200" aria-hidden="true">
    <polygon points="0,1059 354,1059 398,1200 0,1200" fill="var(--navy)"/>
  </svg>
  <p class="abs cta"><span class="accent">Interested in participating?</span><br><span class="plain">Want more information?</span></p>

  <p class="abs link link-email">
    <svg width="16" height="16" viewBox="0 0 16 16"><circle cx="8" cy="8" r="8" fill="#fff"/><rect x="4" y="5" width="8" height="6" fill="none" stroke="var(--ink)" stroke-width="1.2"/><path d="M4 5l4 3.5L12 5" fill="none" stroke="var(--ink)" stroke-width="1.2"/></svg>
    solve@ridgefieldhealth.org
  </p>
  <p class="abs link link-web">
    <svg width="16" height="16" viewBox="0 0 16 16"><circle cx="8" cy="8" r="8" fill="#fff"/><g fill="none" stroke="var(--ink)" stroke-width="1"><circle cx="8" cy="8" r="4.5"/><ellipse cx="8" cy="8" rx="2" ry="4.5"/><line x1="3.5" y1="8" x2="12.5" y2="8"/></g></svg>
    www.solvestudy.org
  </p>

</main>
</body>
</html>
```